Black Matte card with samurai logo which I would like it to be textured and company name on one side and on the other side I would like the company information with the reno (Face logo) Sushi logo. Double Sided card.

majority customers are University students, University sororities and fraternities.

It Company

Reno Sushi
317 W. Harlow Ave
Tucson, AZ 85042
Phone (520)413-6271
Fax (520)357-1846
E-mail: Renosushidesert@mailbox-example.com
FB: Renosushidesert
Twitter: Renosushidesert

• Present Normal

```html
<!DOCTYPE html>
<html lang="en">
<head>
<meta charset="utf-8">
<title>Reno Sushi – Business Card</title>
<link href="https://fonts.googleapis.com/css2?family=Open+Sans:wght@400;600&display=swap" rel="stylesheet">
<style>
  :root {
    --backdrop: #ebe7e1;
    --card-black: #1c1c1c;
    --card-black-edge: #2e2e2e;
    --card-white: #ffffff;
    --sushi-red: #b3301f;
    --ink: #4a4a4a;
    --ink-dark: #222222;
    --white: #ffffff;
    --blade-grey: #e3e3e3;
    --fish-blush: #f1d9d6;
    --social-blue: #3b5a98;
    --social-sky: #5bb6e0;
  }
  * { margin: 0; padding: 0; box-sizing: border-box; }
  html, body {
    width: 1200px;
    height: 1117px;
    overflow: hidden;
    background: var(--backdrop);
    font-family: "Open Sans", sans-serif;
  }
  .card {
    position: absolute;
    overflow: hidden;
  }
  /* Front: black matte side */
  .card-front {
    left: 14px; top: 36px;
    width: 879px; height: 501px;
    background: radial-gradient(ellipse at 48% 40%, var(--card-black-edge) 0%, var(--card-black) 70%);
  }
  .front-brand {
    position: absolute;
    left: 0; right: 0; top: 190px;
    display: flex; align-items: center; justify-content: center; gap: 22px;
  }
  .front-brand .brand-dot {
    width: 46px; height: 46px; border-radius: 50%;
    background: var(--sushi-red);
  }
  .front-brand .brand-name {
    font-size: 64px; font-weight: 600; color: var(--white);
    letter-spacing: 1px;
  }
  .front-url {
    position: absolute;
    left: 0; right: 0; top: 428px;
    text-align: center;
    font-size: 24px; color: var(--white);
    letter-spacing: 2px;
  }
  /* Back: information side */
  .card-back {
    left: 275px; top: 561px;
    width: 879px; height: 501px;
    background: var(--card-white);
    border: 1px solid #9a9a9a;
  }
  .decor-blade {
    position: absolute; left: 13px; top: 20px;
    width: 117px; height: 464px;
    background: var(--blade-grey);
  }
  .decor-fish {
    position: absolute; left: 699px; top: 12px;
    width: 152px; height: 470px;
    background: var(--fish-blush);
  }
  .back-brand {
    position: absolute; left: 0; right: 0; top: 170px;
    display: flex; align-items: center; justify-content: center; gap: 16px;
  }
  .back-brand .brand-dot {
    width: 34px; height: 34px; border-radius: 50%;
    background: var(--sushi-red);
  }
  .back-brand .brand-name {
    font-size: 58px; font-weight: 400; color: var(--sushi-red);
  }
  .contact {
    position: absolute; left: 0; right: 0; top: 340px;
    text-align: center; color: var(--ink);
    font-size: 20px; line-height: 34px;
  }
  .contact-line {
    display: flex; justify-content: center; align-items: center; gap: 8px;
  }
  .contact-line .pair { display: inline-flex; align-items: center; gap: 8px; margin: 0 8px; }
  .icon { width: 18px; height: 18px; flex: none; }
  .social-square { width: 18px; height: 18px; background: var(--social-blue); }
  .social-circle { width: 18px; height: 18px; border-radius: 50%; background: var(--social-sky); }
  .address { margin-top: 10px; font-size: 21px; }
</style>
</head>
<body>

<section class="card card-front" aria-label="Card front">
  <div class="front-brand">
    <span class="brand-dot"></span>
    <span class="brand-name">Reno Sushi</span>
  </div>
  <p class="front-url">www.renosushidesert.example</p>
</section>

<section class="card card-back" aria-label="Card back">
  <div class="decor-blade" role="img" aria-label="Faint grey sword decoration"></div>
  <div class="decor-fish" role="img" aria-label="Faint pink fish decoration"></div>

  <div class="back-brand">
    <span class="brand-dot"></span>
    <span class="brand-name">Reno Sushi</span>
  </div>

  <div class="contact">
    <div class="contact-line">
      <span class="pair">
        <svg class="icon" viewBox="0 0 20 20" aria-hidden="true">
          <circle cx="10" cy="10" r="9" fill="none" stroke="#b3301f" stroke-width="2"/>
          <path d="M7 5 l2 0 l1 3 l-1.5 1 a6 6 0 0 0 3 3 l1 -1.5 l3 1 l0 2 a2 2 0 0 1 -2 1.5 a9 9 0 0 1 -8 -8 a2 2 0 0 1 1.5 -2 z" fill="#b3301f"/>
        </svg>
        (520)413-6271
      </span>
      <span class="pair">
        <svg class="icon" viewBox="0 0 20 20" aria-hidden="true">
          <rect x="5" y="1" width="10" height="18" rx="2" fill="#b3301f"/>
          <rect x="7" y="3" width="6" height="6" fill="#ffffff"/>
          <rect x="7" y="11" width="6" height="5" fill="#f1d9d6"/>
        </svg>
        (520)357-1846
      </span>
    </div>
    <div class="contact-line">
      <svg class="icon" viewBox="0 0 20 20" aria-hidden="true">
        <rect x="1" y="5" width="18" height="12" rx="1" fill="#b3301f"/>
        <path d="M1 5 l9 7 l9 -7" fill="none" stroke="#ffffff" stroke-width="1.6"/>
      </svg>
      Renosushidesert@mailbox-example.com
    </div>
    <div class="contact-line">
      <span class="pair"><span class="social-square"></span>Renosushidesert</span>
      <span class="pair"><span class="social-circle"></span>Renosushidesert</span>
    </div>
    <p class="address">Reno Sushi 317 W. Harlow Ave Tucson, AZ 85042</p>
  </div>
</section>

</body>
</html>
```